Australian Trucking Company Requires Professional Looking Stationary

We require a professional looking stationary design that incorporates our newly designed logo.

Our business, called "Brell Haulage Contracting", provides contracting work, transport and logistics to business in Western Australia particularly with links to the mining sector.

We are a small business looking to expand and our new logo and our new stationary will help develop our brand image in our market place.

Target Market(s)

Businesses and Corporation with links to the Mining Sector

Industry/Entity Type

Small Business

Requirements
Must have
• The letterhead must have the following details:
The new logo

Text saying: "Brell Holdings Pty Ltd (ACN 582 316 907) ATF The Brell Discretionary Trust T/AS"
"ABN 71 834 209 553"
Address "P.O Box 817 Wattlegrove WA, 6958"
Phone: 08 9352 7140
Email: brellhaul@mailbox-example.com.au

The text on the letterhead should be editable as the details are likely to change in the near future. Provision should be made for a website address all though one isn't available at the moment.

The styling, layout and font text is entirely up to the designer.

```html
<!DOCTYPE html>
<html lang="en">
<head>
<meta charset="utf-8">
<title>Brell Haulage Contracting – DL Envelope</title>
<link rel="stylesheet" href="https://fonts.googleapis.com/css2?family=Barlow:wght@400;600&display=swap">
<style>
  :root {
    --backdrop: #d9d6d1;
    --paper: #f4f4f3;
    --band: #3b3b3d;
    --ink: #3a3a3a;
    --mark-grey: #8a8a8c;
  }
  * { margin: 0; padding: 0; box-sizing: border-box; }
  html, body {
    width: 1200px;
    height: 720px;
    overflow: hidden;
    background: var(--backdrop);
  }
  .canvas {
    position: relative;
    width: 1200px;
    height: 720px;
  }
  .envelope {
    position: absolute;
    left: 80px;
    top: 100px;
    width: 1040px;
    height: 520px;
    background: var(--paper);
    box-shadow: 0 10px 30px rgba(0, 0, 0, 0.18);
    display: flex;
    flex-direction: column;
  }
  .envelope__band {
    background: var(--band);
    flex: none;
  }
  .envelope__band--top { height: 12px; }
  .envelope__band--bottom { height: 18px; margin-top: auto; }
  .sender {
    padding: 40px 0 0 48px;
    font-family: "Barlow", sans-serif;
  }
  .brand {
    display: flex;
    align-items: center;
    gap: 12px;
  }
  .brand__square {
    width: 22px;
    height: 22px;
    background: var(--mark-grey);
    flex: none;
  }
  .brand__name {
    color: var(--ink);
    font-weight: 600;
    font-size: 20px;
    line-height: 24px;
  }
  .sender__address {
    margin-top: 16px;
    color: var(--ink);
    font-weight: 400;
    font-size: 14px;
    line-height: 18px;
  }
  .sender__address p:first-child { margin-bottom: 6px; }
</style>
</head>
<body>
<main class="canvas">
  <section class="envelope" aria-label="DL envelope">
    <div class="envelope__band envelope__band--top"></div>
    <div class="sender">
      <div class="brand">
        <div class="brand__square" aria-hidden="true"></div>
        <h1 class="brand__name">Brell Haulage Contracting</h1>
      </div>
      <div class="sender__address">
        <p>P.O Box 817 Wattlegrove WA, 6958</p>
        <p>Brell Holdings Pty Ltd (ACN 582 316 907)</p>
        <p>ATF The Brell Discretionary Trust T/AS</p>
        <p>ABN 71 834 209 553</p>
      </div>
    </div>
    <div class="envelope__band envelope__band--bottom"></div>
  </section>
</main>
</body>
</html>
```